Custom Cabinet Shop Needs a website design

Hi,
We need a website for a Custom Cabinet Shop and Cabinet parts manufacturing business.
The business has two sides to it. One side provides custom Kitchens, vanities, entertainment units, offices and what not to homeowners and contractors.
The 2nd side of the business provides built to order cabinet boxes and other parts required to put together a project to other cabinet shops, small contractors looking to install there own cabinets.
Website will need a Gallery to display work.
Color scheme to go well with logo.
current website is www.brambleoakcustomcabinets.com
being changed to www.brambleoak.ca
Logo Included in attached files.
Tagline "Joinery with Spirit"
Mission Statement "Our passion is to deliver inspired cabinetry solutions to suit all your needs, supported by our phenomenal star class customer service"
The website should convey quality and professionalism.
Thank you.
Homeowners/ Contractors
Entertainment

```html
<!DOCTYPE html>
<html lang="en">
<head>
<meta charset="utf-8">
<title>Brambleoak Custom Cabinets</title>
<link href="https://fonts.googleapis.com/css2?family=Open+Sans:wght@400;600;700&family=Raleway:wght@400;500;600&display=swap" rel="stylesheet">
<style>
:root{
  --orange:#f26a2e;
  --orange-dark:#d9561d;
  --ink:#1c1c1c;
  --text:#333;
  --muted:#666;
  --footer:#333333;
  --footer-base:#2a2a2a;
  --footer-text:#a9a9a9;
  --white:#fff;
}
*{margin:0;padding:0;box-sizing:border-box}
html,body{width:1155px;height:1200px;overflow:hidden;background:var(--white)}
body{position:relative;font-family:"Raleway",sans-serif;color:var(--text)}
.abs{position:absolute}

.brand{display:flex;align-items:center;gap:10px}
.brand-mark{width:22px;height:22px;background:var(--orange)}
.brand-name{font-family:"Raleway",sans-serif;font-weight:600;font-size:27px;letter-spacing:.5px}
.site-header .brand{left:106px;top:44px}
.site-header .brand-name{color:var(--ink)}

.phone{right:105px;top:24px;display:flex;align-items:center;gap:8px;font-size:19px;color:#444}
.main-nav{right:104px;top:62px;display:flex;align-items:center;font-size:14px;font-weight:500;color:#222}
.main-nav a{color:inherit;text-decoration:none;margin-left:42px}
.main-nav a.active{background:var(--orange);color:#fff;padding:5px 9px;border-radius:2px;margin-left:0}
.main-nav a.wide{margin-left:50px}

.hero{left:106px;top:115px;width:943px;height:346px;border-radius:6px;overflow:hidden}
.hero-photo{position:absolute;inset:0;background:linear-gradient(120deg,#6a6258 0%,#8c8379 35%,#5b4b3c 65%,#2e241c 100%)}
.hero svg.panel{position:absolute;left:0;top:0}
.hero-copy{position:absolute;left:25px;top:92px;width:300px;color:#fff}
.hero-copy h1{font-weight:500;font-size:31px;letter-spacing:.3px;margin-bottom:12px}
.hero-copy p{font-size:14px;line-height:18px;padding-left:2px;font-weight:500}
.btn{display:inline-block;background:var(--orange);color:#fff;font-size:13px;font-weight:500;padding:8px 9px;border-radius:3px;margin-top:20px;margin-left:2px}
.hero-dots{position:absolute;left:33px;top:300px;display:flex;gap:5px}
.hero-shadow{left:106px;top:461px;width:943px;height:50px;background:radial-gradient(ellipse 50% 60% at 50% 0,rgba(0,0,0,.22),rgba(0,0,0,0) 70%)}

.promo{top:521px;width:296px;height:128px;border-radius:3px;overflow:hidden;color:#fff}
.promo-media{position:absolute;inset:0}
.promo h2{position:absolute;left:82px;top:35px;font-family:"Open Sans",sans-serif;font-weight:400;font-size:25px;line-height:28px}
.promo .fold{position:absolute;right:0;top:0}
.promo.residential{left:107px}
.promo.residential .promo-media{background:linear-gradient(90deg,#b8805a 0%,#e8844a 45%,#f06a2e 100%)}
.promo.office{left:430px}
.promo.office .promo-media{background:linear-gradient(90deg,#5a5048 0%,#333 45%,#1f1f1f 100%)}
.promo.office h2{left:78px}
.promo.newsletter{left:753px}
.promo.newsletter .promo-media{background:linear-gradient(90deg,#d8cfc5 0%,#b7835a 40%,#8c4a16 100%)}
.promo.newsletter h2{left:108px}

.gallery-title{left:106px;top:691px;font-family:"Open Sans",sans-serif;font-weight:700;font-size:25px;color:#222}
.gallery-lead{left:108px;top:728px;font-family:"Open Sans",sans-serif;font-size:14px;color:#555}
.gallery-arrows{left:1004px;top:724px;display:flex;gap:2px}
.thumb{top:773px;width:218px;height:145px;border-radius:3px}
.thumb.one{left:106px;background:linear-gradient(135deg,#d8d4cc,#8a6a4a 60%,#3a2a20)}
.thumb.two{left:347px;background:linear-gradient(135deg,#3e3a36,#2a2622 60%,#1c1a18)}
.thumb.three{left:589px;background:linear-gradient(180deg,#d9cfc2,#7a3a22 70%,#5a2a18)}
.thumb.four{left:831px;background:linear-gradient(135deg,#b8b0a4,#6e6254 50%,#2c241e)}
.thumb-action{position:absolute;left:79px;top:44px;width:58px;height:58px;border-radius:50%;background:rgba(20,20,20,.85);display:flex;align-items:center;justify-content:center}

.site-footer{left:0;top:962px;width:1155px;height:185px;background:var(--footer)}
.site-footer .brand{position:absolute;left:106px;top:80px}
.site-footer .brand-name{color:#fff}
.footer-col{position:absolute;top:25px;font-size:13px;color:var(--footer-text)}
.footer-col h3{font-size:14px;font-weight:600;color:#f0f0f0;margin-bottom:14px}
.footer-col li{list-style:none;line-height:20px}
.topics{left:382px}
.contact{left:553px;font-size:12.5px}
.contact li{line-height:20px}
.join{left:802px}
.signup{display:flex;width:247px;height:34px;background:#2b2b2b;border:1px solid #444;border-radius:3px;align-items:center;justify-content:space-between;padding:0 2px 0 9px}
.signup span{font-style:italic;font-size:11px;color:#777}
.signup b{background:#111;color:#fff;font-weight:500;font-size:13px;padding:7px 13px;border-radius:2px}
.social{display:flex;gap:10px;margin-top:20px;margin-left:59px}
.social i{display:block;width:30px;height:30px;border-radius:2px;background:#555}
.social i:nth-child(odd){background:var(--orange)}
.footer-base{left:0;top:1147px;width:1155px;height:53px;background:var(--footer-base);text-align:center;line-height:53px;font-size:12px;color:#999}
</style>
</head>
<body>

<header class="site-header">
  <div class="brand abs"><span class="brand-mark"></span><span class="brand-name">BRAMBLEOAK</span></div>
  <div class="phone abs">
    <svg width="20" height="20" viewBox="0 0 24 24"><path fill="#555" d="M6.6 10.8a15.1 15.1 0 0 0 6.6 6.6l2.2-2.2a1 1 0 0 1 1-.25 11.4 11.4 0 0 0 3.6.57 1 1 0 0 1 1 1V20a1 1 0 0 1-1 1A17 17 0 0 1 3 4a1 1 0 0 1 1-1h3.5a1 1 0 0 1 1 1c0 1.25.2 2.45.57 3.57a1 1 0 0 1-.25 1z"/></svg>
    <span>555-014-2160</span>
  </div>
  <nav class="main-nav abs">
    <a class="active" href="#">Home</a>
    <a href="#">Gallery</a>
    <a class="wide" href="#">Services</a>
    <a class="wide" href="#">Warranty</a>
    <a href="#">Contact</a>
  </nav>
</header>

<section class="hero abs">
  <div class="hero-photo" role="img" aria-label="Photo of a modern kitchen with granite island and bar stools"></div>
  <svg class="panel" width="943" height="346" viewBox="0 0 943 346">
    <defs>
      <linearGradient id="panelFill" x1="0" y1="0" x2="0" y2="1">
        <stop offset="0" stop-color="#2e2e2e"/><stop offset="1" stop-color="#0c0c0c"/>
      </linearGradient>
    </defs>
    <path d="M0 0H372C335 60 372 130 350 190C325 250 305 300 335 346H0Z" fill="rgba(255,255,255,.35)"/>
    <path d="M0 0H356C322 60 356 130 334 190C310 250 292 300 322 346H0Z" fill="url(#panelFill)"/>
  </svg>
  <div class="hero-copy">
    <h1>Joinery with Spirit</h1>
    <p>Lorem ipsum dolor sita amet, consectetur adip iscing elit, sed do eiusmod tempor incididuntut.</p>
    <span class="btn">Read More</span>
  </div>
  <div class="hero-dots">
    <svg width="20" height="20" viewBox="0 0 24 24"><path d="M12 2l2.9 6.9 7.1.6-5.4 4.7 1.7 7-6.3-3.9-6.3 3.9 1.7-7L2 9.5l7.1-.6z" fill="none" stroke="#fff" stroke-width="1.4"/></svg>
    <svg width="20" height="20" viewBox="0 0 24 24"><path d="M12 2l2.9 6.9 7.1.6-5.4 4.7 1.7 7-6.3-3.9-6.3 3.9 1.7-7L2 9.5l7.1-.6z" fill="none" stroke="#f26a2e" stroke-width="1.6"/></svg>
    <svg width="20" height="20" viewBox="0 0 24 24"><path d="M12 2l2.9 6.9 7.1.6-5.4 4.7 1.7 7-6.3-3.9-6.3 3.9 1.7-7L2 9.5l7.1-.6z" fill="none" stroke="#fff" stroke-width="1.4"/></svg>
    <svg width="20" height="20" viewBox="0 0 24 24"><path d="M12 2l2.9 6.9 7.1.6-5.4 4.7 1.7 7-6.3-3.9-6.3 3.9 1.7-7L2 9.5l7.1-.6z" fill="none" stroke="#fff" stroke-width="1.4"/></svg>
  </div>
</section>
<div class="hero-shadow abs"></div>

<article class="promo residential abs">
  <div class="promo-media" role="img" aria-label="Warm-lit residential kitchen with bar seating"></div>
  <h2>Residential<br>Custom Cabinets</h2>
  <svg class="fold" width="36" height="36" viewBox="0 0 36 36"><path d="M0 0H36V36Z" fill="#fff"/><path d="M0 0L36 36C22 30 6 16 0 0Z" fill="#e0a070"/></svg>
</article>
<article class="promo office abs">
  <div class="promo-media" role="img" aria-label="Home office with built-in desk and shelving"></div>
  <h2>Office<br>Custom Cabinets</h2>
  <svg class="fold" width="36" height="36" viewBox="0 0 36 36"><path d="M0 0H36V36Z" fill="#fff"/><path d="M0 0L36 36C22 30 6 16 0 0Z" fill="#111"/></svg>
</article>
<article class="promo newsletter abs">
  <div class="promo-media" role="img" aria-label="Keyboard with a newsletter key"></div>
  <h2>Subscribe<br>to Newsletter</h2>
  <svg class="fold" width="36" height="36" viewBox="0 0 36 36"><path d="M0 0H36V36Z" fill="#fff"/><path d="M0 0L36 36C22 30 6 16 0 0Z" fill="#c27a40"/></svg>
</article>

<h2 class="gallery-title abs">Our Gallery</h2>
<p class="gallery-lead abs">Lorem ipsum dolor sit amet, consectetur adipiscing elit,</p>
<div class="gallery-arrows abs">
  <svg width="21" height="21" viewBox="0 0 21 21"><circle cx="10.5" cy="10.5" r="10.5" fill="#1a1a1a"/><path d="M12.5 6.5v8l-5-4z" fill="#fff"/></svg>
  <svg width="21" height="21" viewBox="0 0 21 21"><circle cx="10.5" cy="10.5" r="10.5" fill="#1a1a1a"/><path d="M8.5 6.5v8l5-4z" fill="#fff"/></svg>
</div>
<div class="thumb one abs" role="img" aria-label="Open kitchen with dark island and pendant lights"></div>
<div class="thumb two abs" role="img" aria-label="Dining room with dark wood furniture">
  <span class="thumb-action"><svg width="16" height="16" viewBox="0 0 24 24"><path d="M3 17.2V21h3.8L17.8 10l-3.8-3.8zM20.7 7a1 1 0 0 0 0-1.4l-2.3-2.3a1 1 0 0 0-1.4 0l-1.8 1.8 3.8 3.8z" fill="#fff"/></svg></span>
</div>
<div class="thumb three abs" role="img" aria-label="Cherry wood entertainment unit with television"></div>
<div class="thumb four abs" role="img" aria-label="Kitchen with stainless appliances and granite island"></div>

<footer class="site-footer abs">
  <div class="brand"><span class="brand-mark"></span><span class="brand-name">BRAMBLEOAK</span></div>
  <div class="footer-col topics">
    <h3>Topic</h3>
    <ul><li>Advice</li><li>About</li><li>Contact</li><li>Privacy Policy</li><li>Terms &amp; Conditons</li></ul>
  </div>
  <div class="footer-col contact">
    <h3>Contact Info</h3>
    <ul><li>4810 Cedar Line Road 17</li><li>Millbrook Valley, Alberta</li><li>T0X 4B2</li><li>Tel: 555-014-2160 or 555-019-1052</li></ul>
  </div>
  <div class="footer-col join">
    <h3>Join Our Newsletter</h3>
    <div class="signup"><span>Enter your email address</span><b>Subscribe</b></div>
    <div class="social" aria-label="Social links"><i></i><i></i><i></i><i></i><i></i></div>
  </div>
</footer>
<div class="footer-base abs">Copyright © 2015 Brambleoak Custom Cabinets. Ltd. All rights reserved.</div>

</body>
</html>
```